Redesign This Psychology Website

We would like a slight redesign of this successful psychology (relationship counselling) website:

www.TheKelvaleClinic.com.au

We are updating the website, and we'd like a slight refresh of the design and style.

Please keep to very similar colours, and use the same logo. We're looking for around 10 page templates, however the main one is the home page.

Keep in mind, this website already converts quite well, so we want a new, fresh design in keeping with this one. Please don't bother designing something too extremely different.

thanks :)

Target Market(s)

couples who are looking for relationship counselling. Men and women, 25 - 70, across Australia

Industry/Entity Type

Psychology

Number of Pages Required

5+ page

Font styles to use
Sans Serif

Colors
87cfc6
b7a5cd
ec1f27
ffffff
cee9f5

Requirements
Must have
• a similar look to the current design, just looking for a slight refresh.
• Search bar
• Areas for lots of photos
• same logo
• lots of content areas
Nice to have
• great content areas, where we can display a lot of content and our areas.
Should not have
• no colors like orange, etc.
• should not have a totally different feel.

```html
<!DOCTYPE html>
<html lang="en">
<head>
<meta charset="utf-8">
<title>The Kelvale Clinic – Relationship Counselling</title>
<link href="https://fonts.googleapis.com/css2?family=Questrial&family=Open+Sans:wght@400;600;700&display=swap" rel="stylesheet">
<style>
:root{
  --teal:#87cfc6;
  --teal-dark:#6fc2b8;
  --lilac:#b7a5cd;
  --red:#ec1f27;
  --white:#ffffff;
  --ink:#333333;
  --muted:#555555;
  --dark:#262626;
  --grey-bg:#f1f1f1;
  --map:#ef9d9c;
}
*{box-sizing:border-box;margin:0;padding:0}
html,body{width:1200px;height:4457px;overflow:hidden;background:var(--white)}
body{font-family:"Open Sans",sans-serif;color:var(--ink);font-size:11px;line-height:1.9}
.wrap{width:878px;margin:0 auto;position:relative}
h2{font-family:"Questrial",sans-serif;font-weight:400;font-size:24px;color:var(--ink)}
.btn{display:inline-block;background:var(--teal);color:var(--white);border-radius:17px;font-family:"Questrial",sans-serif;font-size:13px;padding:0 18px;height:33px;line-height:33px}

/* top bar */
.topbar{height:42px;background:var(--dark);color:#ddd;font-size:10px}
.topbar .wrap{display:flex;align-items:center;height:42px;justify-content:space-between}
.topbar .links span{margin-right:12px}
.topbar .links em{font-style:normal;color:var(--teal)}
.topbar .search{width:230px;height:26px;background:var(--white);color:#999;font-style:italic;padding-left:10px;line-height:26px;position:relative}
.topbar .search svg{position:absolute;right:8px;top:7px}

/* header */
.header{height:114px}
.header .wrap{height:114px}
.logo{position:absolute;left:0;top:22px;display:flex;align-items:center;gap:10px}
.logo .dot{width:46px;height:46px;border-radius:50%;background:var(--teal)}
.logo .name{font-family:"Questrial",sans-serif;font-size:30px;color:var(--teal-dark);line-height:1}
.logo .tag{font-size:12px;color:var(--teal-dark);line-height:1.4}
.callus{position:absolute;right:0;top:16px;color:var(--red);font-family:"Questrial",sans-serif;font-size:19px;display:flex;align-items:center;gap:8px}
.mainnav{position:absolute;right:0;top:66px;display:flex;gap:46px;font-size:11px;font-weight:600;color:#444}
.mainnav .on{color:var(--red)}

.subnav{height:55px;background:var(--teal);color:var(--white);font-family:"Questrial",sans-serif;font-size:14px}
.subnav .wrap{display:flex;gap:37px;height:55px;align-items:center;padding-left:27px}

.hero{height:529px;background:linear-gradient(110deg,#b9b2a8,#7f8a99 45%,#d7cdc2);position:relative}
.hero .arrow{position:absolute;top:230px}
.hero .play{position:absolute;left:554px;top:413px}

/* intro */
.intro{height:242px;background:#f4f4f4;text-align:center;padding-top:42px}
.intro p{width:720px;margin:16px auto 0;font-size:10px;line-height:2.2;color:var(--muted)}

/* services */
.services{height:543px;padding-top:55px}
.cards{display:flex;gap:16px}
.card{width:207px;height:427px;border:1px solid #e2e2e2;text-align:center}
.card .pic{height:170px;background:linear-gradient(135deg,#c9b6a5,#8c8077)}
.card h3{font-family:"Questrial",sans-serif;font-weight:400;font-size:15px;line-height:1.6;margin:22px 0 0;color:var(--ink)}
.card .bar{width:30px;height:2px;background:var(--teal);margin:10px auto 14px}
.card p{font-size:10px;line-height:2.1;color:var(--muted);padding:0 24px}
.card .btn{margin-top:18px}

/* finder */
.finder{height:213px;background:var(--lilac);text-align:center;padding-top:42px}
.finder h2{color:var(--white)}
.finder form{display:flex;justify-content:center;align-items:center;margin-top:22px;gap:7px}
.field{height:34px;border-radius:17px;background:var(--white);font-size:10px;font-style:italic;color:#555;text-align:left;padding-left:18px;line-height:34px;position:relative}
.field.type{width:267px}
.field.loc{width:197px}
.field.post{width:199px}
.or{color:var(--white);font-size:10px;font-weight:700;margin:0 3px}
.finder .go{width:100px;height:34px;border-radius:17px;background:var(--teal);color:var(--white);font-size:10px;font-weight:700;line-height:34px}

/* psychologists */
.team{height:375px;padding-top:40px}
.team .text{width:450px}
.team p{font-size:10px;line-height:2.1;color:var(--muted);margin-top:10px}
.team ul{list-style:none;columns:2;width:400px;margin-top:20px;font-size:10px;line-height:22px}
.team li::before{content:"»";color:var(--red);margin-right:10px;font-weight:700}
.team .pic{position:absolute;left:480px;top:5px;width:396px;height:263px;background:linear-gradient(135deg,#d6d1cc,#a3a1a6)}

/* photos */
.photos{height:506px;background:var(--grey-bg);text-align:center;padding-top:38px}
.grid{display:grid;grid-template-columns:repeat(3,278px);gap:18px 22px;margin-top:22px}
.grid div{height:162px;background:linear-gradient(135deg,#c8c1b8,#8d8f96)}

/* approach */
.approach{height:390px;padding-top:61px}
.approach .pic{width:396px;height:261px;background:linear-gradient(135deg,#6b7180,#c8bfb6)}
.approach .text{position:absolute;left:434px;top:0;width:444px}
.approach p{font-size:10px;line-height:2.1;color:var(--muted);margin-top:12px}
.approach a{display:block;color:var(--red);font-family:"Questrial",sans-serif;font-size:14px;text-decoration:none;line-height:1.7}

/* about */
.about{height:385px;background:var(--teal);color:var(--white);text-align:center;padding-top:44px}
.about h2{color:var(--white)}
.about .quote{font-family:"Questrial",sans-serif;font-size:17px;margin-top:6px}
.about p{width:650px;margin:10px auto 0;font-size:10px;line-height:2.2}
.person{display:flex;align-items:center;justify-content:center;gap:14px;margin-top:26px;text-align:left}
.person .avatar{width:114px;height:114px;border-radius:50%;background:linear-gradient(135deg,#f1dfa6,#c7a374);border:3px solid var(--white)}
.person b{display:block;font-size:14px}
.person span{display:block;font-family:"Questrial",sans-serif;font-size:15px}
.person small{font-size:9px}

/* blog */
.blog{height:553px;text-align:center;padding-top:42px}
.posts{display:flex;gap:37px;text-align:left;margin-top:22px}
.post{width:268px}
.post .pic{height:173px;background:linear-gradient(135deg,#a69d96,#d7cbc3)}
.post .date{font-size:10px;margin-top:18px;color:var(--muted)}
.post h3{font-family:"Questrial",sans-serif;font-weight:400;font-size:15px;line-height:1.7;margin-top:8px;height:52px}
.post p{font-size:10px;line-height:2.1;color:var(--muted);margin-top:2px}
.post .btn{margin-top:14px}

/* locations */
.locations{height:87px;background:#f3f3f3}
.locations .wrap{display:flex;align-items:center;justify-content:space-between;height:87px}
.select{width:243px;height:30px;background:var(--white);display:flex;align-items:center;font-size:10px;color:#999;position:relative;padding-left:44px}
.select .ico{position:absolute;left:8px;top:7px;width:24px;height:16px;border-radius:8px;background:#c9c9c9}
.select .drop{position:absolute;right:0;top:0;width:36px;height:30px;background:var(--red)}
.select .drop svg{margin:11px}
.map{height:280px;background:linear-gradient(180deg,#f2aaa9,var(--map))}

/* footer */
.footer{height:143px;text-align:center;font-size:10px;padding-top:22px;color:#333}
.footer .social{display:flex;justify-content:center;gap:6px;margin-top:12px}
.footer .social span{width:28px;height:28px;border-radius:50%;background:var(--teal)}
</style>
</head>
<body>

<div class="topbar"><div class="wrap">
  <div class="links"><span>JOIN OUR <em>ASSOCIATE PROGRAM</em></span><span>|</span><span>MARRIAGE COUNSELLING</span><span>|</span><span>RELATIONSHIP COUNSELLING</span></div>
  <div class="search">Search
    <svg width="12" height="12" viewBox="0 0 12 12"><circle cx="5" cy="5" r="3.5" fill="none" stroke="#222" stroke-width="1.6"/><line x1="7.6" y1="7.6" x2="11" y2="11" stroke="#222" stroke-width="1.8"/></svg>
  </div>
</div></div>

<header class="header"><div class="wrap">
  <div class="logo"><span class="dot"></span><div><div class="name">Kelvale Clinic</div><div class="tag">helping you create loving relationships</div></div></div>
  <div class="callus">
    <svg width="16" height="16" viewBox="0 0 16 16"><path d="M3 1l3 3-2 2c1 2 3 4 6 6l2-2 3 3-2 2C7 15 1 9 1 3z" fill="#ec1f27"/></svg>
    CALL US ON 1300 555 019</div>
  <nav class="mainnav"><span class="on">HOME</span><span>ABOUT</span><span>RESOURCES</span><span>BLOG</span><span>SHOP</span><span>CART &#128722;</span></nav>
</div></header>

<nav class="subnav"><div class="wrap"><span>Counselling Types</span><span>Relationship Counselling Locations</span><span>Sex Therapy Locations</span><span>Quizzes</span><span>F.A.Q.'s</span><span>Contact</span></div></nav>

<section class="hero" role="img" aria-label="Photo of a couple talking with a counsellor on a sofa">
  <svg class="arrow" style="left:30px" width="36" height="70" viewBox="0 0 36 70"><polyline points="34,2 2,35 34,68" fill="none" stroke="#fff" stroke-width="2"/></svg>
  <svg class="arrow" style="right:30px" width="36" height="70" viewBox="0 0 36 70"><polyline points="2,2 34,35 2,68" fill="none" stroke="#fff" stroke-width="2"/></svg>
  <svg class="play" width="92" height="92" viewBox="0 0 92 92" style="top:186px"><circle cx="46" cy="46" r="43" fill="none" stroke="#fff" stroke-width="4"/><polygon points="36,28 66,46 36,64" fill="#fff"/></svg>
</section>

<section class="intro">
  <h2>We Specialise in Relationship &amp; Marriage Counselling</h2>
  <p>At the Kelvale Clinic, we are a group of PSYCHOLOGISTS, Australia wide who are passionate about relationships and helping you with yours. Our vision is to provide the most highly regarded and comprehensive marriage counselling and relationship counselling, and sex therapy in Australia, at reasonable and affordable rates. When we are experiencing relationship and marriage problems, there can be a lot of pain and confusion, and it can often be difficult to cope with the other areas of our lives when we are struggling with problems with our partner.</p>
</section>

<section class="services"><div class="wrap cards">
  <article class="card"><div class="pic" role="img" aria-label="Photo of a couple in a tense conversation"></div><h3>RELATIONSHIP<br>COUNSELLING</h3><div class="bar"></div><p>Communication, Recovering from an affair, Loss of intimacy &amp; love, Power battles, Feeling like friends, not lovers.</p><span class="btn">Read More</span></article>
  <article class="card"><div class="pic" role="img" aria-label="Photo of a couple sitting apart on a bed"></div><h3>SEX THERAPY<br>COUNSELLING</h3><div class="bar"></div><p>Communication, Recovering from an affair, Loss of intimacy &amp; love, Power battles, Feeling like friends, not lovers.</p><span class="btn">Read More</span></article>
  <article class="card"><div class="pic" role="img" aria-label="Photo of a distressed woman and a counsellor"></div><h3>ANGER MANAGEMENT<br>COUNSELLING</h3><div class="bar"></div><p>Communication, Recovering from an affair, Loss of intimacy &amp; love, Power battles, Feeling like friends, not lovers.</p><span class="btn">Read More</span></article>
  <article class="card"><div class="pic" role="img" aria-label="Photo of a couple arguing"></div><h3>NARCISSISM<br>COUNSELLING</h3><div class="bar"></div><p>Communication, Recovering from an affair, Loss of intimacy &amp; love, Power battles, Feeling like friends, not lovers.</p><span class="btn">Read More</span></article>
</div></section>

<section class="finder">
  <h2>Find Our Psychologist Near You</h2>
  <form>
    <div class="field type">Type of Counselling <svg style="position:absolute;right:14px;top:15px" width="8" height="5" viewBox="0 0 8 5"><polygon points="0,0 8,0 4,5" fill="#666"/></svg></div>
    <div class="field loc">Location</div>
    <span class="or">OR</span>
    <div class="field post">Postcode</div>
    <div class="go">SEARCH</div>
  </form>
</section>

<section class="team"><div class="wrap">
  <div class="text">
    <h2>Our Kelvale Relationship Psychologists</h2>
    <p>Our team of 75 hand chosen Registered Psychologists in 81 locations Australia wide, are individually selected for their knowledge, experience, compassion, and unbiased approach to marriage counselling and sexual therapy.</p>
    <ul>
      <li>Affairs</li><li>Controlling behaviour</li><li>Verbal abuse</li><li>Imbalance of power</li><li>Lack of intimacy</li><li>Poor communication</li><li>Loss of love</li>
      <li>Relationship neglect</li><li>Sexual problems</li><li>Problems from childhood</li><li>Problems with parenting your children</li><li>Step children and in-laws</li><li>All forms of family problems</li><li>Anger management problems</li>
    </ul>
  </div>
  <div class="pic" role="img" aria-label="Photo of an older couple in a counselling session"></div>
</div></section>

<section class="photos">
  <h2>Our Photos</h2>
  <div class="wrap grid">
    <div role="img" aria-label="Photo of a couple talking on a sofa"></div>
    <div role="img" aria-label="Photo of a couple sitting apart"></div>
    <div role="img" aria-label="Photo of a smiling woman in a session"></div>
    <div role="img" aria-label="Photo of a mature couple"></div>
    <div role="img" aria-label="Photo of a woman speaking to a man"></div>
    <div role="img" aria-label="Photo of a hotel room with a couple"></div>
  </div>
</section>

<section class="approach"><div class="wrap">
  <div class="pic" role="img" aria-label="Photo of a young couple sitting together"></div>
  <div class="text">
    <h2>Our Relationship Counselling Approach</h2>
    <p>It is an important part of our policy to take a very positive approach to our relationship counselling. We feel it is important to really understand the problems and perspectives of each of you, and at the same time, we find that most couples are looking to find a positive action plan and way through their problems to make changes which have a positive impact and a real sense of hope for their relationship.</p>
    <p>Read more about our approach to counselling in our relationship counselling sessions, and frequently asked questions about the relationship and marriage counselling process.</p>
    <div style="margin-top:14px"><a>Our Relationship Counselling Locations across Australia</a><a>Take our Kelvale Relationship Assessment</a></div>
  </div>
</div></section>

<section class="about">
  <h2>About Psychologist</h2>
  <div class="quote">“ At the end of our life, what matters most is how well did we love”</div>
  <p>It can be difficult not to feel quite negative about your relationship when you are experiencing many problems with it. An important part of our couples counselling is to give each of you the opportunity to share what are the problems and issues for you in your relationship. In helping you to resolve these problems, we find it is important for our approach to be as positive as possible.</p>
  <div class="person">
    <div class="avatar" role="img" aria-label="Portrait photo of the clinic director"></div>
    <div><b>Maren Doyle</b><span>Director – Psychologist</span><small>Grad Dip Psych, Post Grad Dip Psych, B Ed, Dip Teach, MAPS</small></div>
  </div>
</section>

<section class="blog">
  <h2>Latest Blog Posts</h2>
  <div class="wrap posts">
    <article class="post"><div class="pic" role="img" aria-label="Photo of a stressed woman and a man"></div><div class="date">February 24, 2017</div><h3>What can I do if I'm living<br>with a Narcissist?</h3><p>If you are in a relationship with a Narcissist, in his/her mind, you are an extension of him/her and he/she must always win, so his/her eruptions of temper and ego and devaluations.</p><span class="btn">Read More</span></article>
    <article class="post"><div class="pic" role="img" aria-label="Photo of an upset woman and a man"></div><div class="date">February 24, 2017</div><h3>How Do I Know If I'm With a<br>Narcissist?</h3><p>If you are in a relationship with a Narcissist, in his/her mind, you are an extension of him/her and he/she must always win, so his/her eruptions of temper and ego and devaluations.</p><span class="btn">Read More</span></article>
    <article class="post"><div class="pic" role="img" aria-label="Photo of a couple in disagreement"></div><div class="date">February 24, 2017</div><h3>Letter for a Partner Doubtful<br>About Relationship.</h3><p>If you are in a relationship with a Narcissist, in his/her mind, you are an extension of him/her and he/she must always win, so his/her eruptions of temper and ego and devaluations.</p><span class="btn">Read More</span></article>
  </div>
</section>

<section class="locations"><div class="wrap">
  <h2>Our Relationship Counselling Locations across Australia</h2>
  <div class="select"><span class="ico"></span>Please Select Locations<span class="drop"><svg width="14" height="8" viewBox="0 0 14 8"><polygon points="0,0 14,0 7,8" fill="#fff"/></svg></span></div>
</div></section>

<div class="map" role="img" aria-label="Map of Australia with pins marking counselling locations"></div>

<footer class="footer">
  <div>© Copyright The Kelvale Clinic 2017 Visit us on our social pages</div>
  <div>Privacy Policy Terms &amp; Conditions Site Map Associate Psychologists Program Contact Us</div>
  <div class="social"><span></span><span></span><span></span><span></span></div>
</footer>

</body>
</html>
```